Las Vegas Tour guide needs website of future for physical and selfguided assets

Neon Drifters is the parent site to my Las Vegas tour operation. Within this is a physical walking tour called Whispers and the Racket, the site traffic driver where I tell history with a paranormal twist. The legacy site can be seen at spookyroutewalks.com.
The Neon Drifters app has self guided tours called Desert Hop Trail/Whispers and The Racket Retold/Calloway Row Stroll. Rivano is a 3rd party tour company I have partnered with to sale self-guided tours with a scavenger hunt theme.
I like black and pink and pistachio green colors however am flexible in theme. Colors should follow Vegas 50-60s aesthetics. The “Greetings From Silver Gulch Marker” should not be considered as design inspiration. 95% of traffic is on mobile. Final design should be easy to understand guided versus self-guided option. Show cross promotion links for digital assets/physical tour. Rivano content tbd by end of week 9 Aug 2021
sites i like
nationalspiritstrolls.com
heronsandshades.com
oldportphantomtrips.net
Updates

Needs a book now at top, or floating like lorvantrips. Less busy and stay away from using photos. I have included more websites for inspiration. I would like a mashup of the two sites eerieechoplace and lorvantrips. I am unsure what some of your designs would look like on a mobile screen. Please screenshot that. https://eerieechoplace.com/ https://www.lorvantrips.com/ https://k7vrx.com/ https://bqspecters.com/ https://bluefinjaunts.com/tours/new-york-city/shades-of-pellham-corner/

Family member hospitalized need extra time to review

Target Market(s)

Tourist 25+

Industry/Entity Type

Travel. Tour guide.

Coding

Coded - Design and coding required

Number of Pages Required

5+ page

Font styles to use
Serif

Colors
00AB8E
00BBA5
67D7C9
C6EFE9
E9F9F6
59FF00
82FF00
B8FF75
E3FFCB
F4FFEA
EB3D1F
EC4F4E
F09395
F8D3D4
FCEDEE
E54698
E96AAD
F1A4CE
F9D9EA
FCEFF6

Requirements
Must have
• Cross promotion between physical tour and digital
Nice to have
• sliver button like ads as breaks between tour info
Should not have
• "Greetings from Silver Gulch Marker". no photos. no animation.

```html
<!DOCTYPE html>
<html lang="en">
<head>
<meta charset="utf-8">
<title>Calloway Row Walking Tour</title>
<link rel="stylesheet" href="https://fonts.googleapis.com/css2?family=Blinker:wght@600;700&family=Mulish:wght@400;600;700&display=swap">
<style>
:root{
  --teal:#00a88a;
  --teal-bright:#19b3a0;
  --mint-bg:#e9f9f6;
  --red:#eb3d1f;
  --lime:#7be000;
  --gold:#f2b705;
  --pink:#e54698;
  --ink:#3c3c3c;
  --black:#000;
  --white:#fff;
  --orange:#ef5a0f;
  --heading:"Blinker",sans-serif;
  --body:"Mulish",sans-serif;
}
*{margin:0;padding:0;box-sizing:border-box}
html,body{width:1200px;height:2254px;overflow:hidden;background:var(--white)}
body{position:relative;font-family:var(--body);color:var(--ink)}
.abs{position:absolute}
.center{left:0;width:1200px;text-align:center}

/* hero */
.hero{left:0;top:0;width:1200px;height:663px;
  background:linear-gradient(180deg,#3a3434 0%,#4a3c38 40%,#5a3a30 70%,#2a2424 100%)}
.nav{top:24px;left:0;width:1200px;display:flex;justify-content:center;gap:58px;
  font-family:var(--body);font-weight:700;font-size:14.5px;color:var(--white)}
.nav span:first-child{margin-left:-40px}
.brand-mark{left:531px;top:116px;width:138px;height:138px;border-radius:50%;
  background:linear-gradient(180deg,#2fd8e6 0%,#f7d21c 40%,#f27a12 70%,#e23a1a 100%)}
.brand-name{font-family:var(--heading);font-weight:700;color:var(--orange);font-size:40px;line-height:1}
.hero-name{top:270px}
.hero-line{font-family:var(--heading);font-weight:600;font-size:37px;line-height:1}
.hero-l1{top:382px}
.hero-l1 .beer{color:var(--red);margin-right:22px}
.hero-l1 .racket{color:var(--lime)}
.hero-l2{top:432px;color:var(--teal-bright)}
.hero-sub{top:478px;font-family:var(--body);font-weight:700;color:var(--gold);font-size:17px}
.hero-sub .date{font-size:25px;font-weight:600}
.hero-sub sup{font-size:20px}

/* section headings */
.section-title{font-family:var(--heading);font-weight:600;color:var(--teal)}
.rule{width:70px;height:2px;background:var(--red);left:565px}

/* about */
.about-title{top:733px;font-size:39px}
.about-rule{top:789px}
.about-copy{left:180px;width:840px;top:810px;text-align:center;font-size:14px;line-height:25.4px;color:#444}
.about-copy p+p{margin-top:6px}
.cta{left:524px;top:965px;width:152px;height:42px;background:var(--pink);color:var(--white);
  font-family:var(--heading);font-weight:600;font-size:16px;display:flex;align-items:center;justify-content:center}

/* reviews */
.reviews{left:0;top:1095px;width:1200px;height:470px;background:var(--mint-bg)}
.reviews-title{top:1169px;font-size:46px}
.reviews-rule{top:1234px}
.review-card{top:1292px;width:283px;height:170px;background:var(--white);border-radius:0 0 22px 0;
  box-shadow:0 4px 14px rgba(0,0,0,.06);padding:16px 18px}
.stars{display:flex;gap:2px}
.quote-mark{right:24px;top:-14px}
.review-text{margin-top:14px;font-size:12.6px;line-height:21px;color:#555}
.reviewer{margin-top:13px;font-size:13.5px;font-weight:700;color:#111}
.slider-btn{top:1359px;width:35px;height:35px;border-radius:50%;display:flex;align-items:center;justify-content:center}
.slider-prev{left:70px;background:var(--white);box-shadow:0 2px 8px rgba(0,0,0,.08)}
.slider-next{left:1095px;background:#1f9a5c}

/* tickets */
.tickets{top:1638px;font-family:var(--heading);font-weight:600;color:var(--teal);font-size:49px;line-height:57px}
.tickets svg{vertical-align:-6px;margin:0 8px}

/* footer */
.footer{left:0;top:1834px;width:1200px;height:420px;background:var(--black)}
.contact-box{top:1917px;width:213px;height:154px;border:1px solid #333;color:var(--white);text-align:center}
.contact-box .label{font-size:16px;margin-top:8px}
.contact-box .value{font-size:13px;margin-top:4px}
.footer-mark{left:530px;top:1882px;width:132px;height:132px;border-radius:50%;
  background:linear-gradient(180deg,#2fd8e6 0%,#f7d21c 40%,#f27a12 70%,#e23a1a 100%)}
.footer-name{top:2030px}
.follow{top:2144px;left:0;width:1200px;display:flex;justify-content:center;align-items:center;gap:8px}
.follow-text{font-family:var(--heading);font-weight:600;color:#1fd0dc;font-size:25px;margin-right:2px}
.follow-text small{font-size:14px}
.social{width:36px;height:31px;background:#1c1c1c;border-radius:2px}
.footer-rule{left:147px;top:2180px;width:917px;height:1px;background:#2a2a2a}
.copyright{top:2194px;font-size:12.5px;color:#ccc}
.copyright b{color:var(--white);font-weight:600}
</style>
</head>
<body>

<!-- hero -->
<div class="abs hero" role="img" aria-label="Dim evening street scene under a lit canopy with neon storefronts and visitors"></div>
<nav class="abs nav">
  <span>Whispers And The Racket Las Vegas Walking Tour</span>
  <span>Desert Hop Trail</span>
  <span>Neon Drifters</span>
</nav>
<div class="abs brand-mark" role="img" aria-label="Tour emblem: cocktail glass over a striped desert sunset"></div>
<div class="abs center brand-name hero-name">Calloway Row</div>
<div class="abs center hero-line hero-l1"><span class="beer">Desert Hop Trail</span><span class="racket">Whispers &amp; The Racket Retold</span></div>
<div class="abs center hero-line hero-l2">Calloway Row Stroll</div>
<div class="abs center hero-sub">Rivano Content TBD By End of Week <span class="date">9<sup>th</sup> Aug 2021</span></div>

<!-- about -->
<h2 class="abs center section-title about-title">About Calloway Row Walking Tour</h2>
<div class="abs rule about-rule"></div>
<div class="abs about-copy">
  <p>Lorem ipsum dolor sit amet, consectetuer adipiscing elit, sed diam nonummy nibh euismod tincidunt ut laoreet dolore magna aliquam erat volutpat. Ut wisi enim ad minim veniam, quis nostrud exerci tation ullamcorper suscipit lobortis nisl ut aliquip ex ea commodo consequat. Duis autem vel eum iriure dolor in hendrerit in vulputate velit esse.</p>
  <p>Lorem ipsum dolor sit amet, consectetuer adipiscing elit, sed diam nonummy nibh euismod tincidunt ut laoreet dolore magna aliquam erat volutpat. Ut wisi enim ad minim veniam, quis nostrud exerci tation.</p>
</div>
<a class="abs cta">Contact Us Today</a>

<!-- reviews -->
<section class="abs reviews"></section>
<h2 class="abs center section-title reviews-title">Customer Reviews</h2>
<div class="abs rule reviews-rule"></div>

<div class="abs review-card" style="left:143px">
  <svg class="abs quote-mark" width="44" height="40" viewBox="0 0 44 40"><path d="M0 0h18v20l-8 18H2l6-16H0zM24 0h18v20l-8 18h-8l6-16h-8z" fill="var(--orange)"/></svg>
  <div class="stars"><svg width="70" height="11" viewBox="0 0 70 11" fill="var(--gold)"><g id="s"><polygon points="5.5,0 7,3.8 11,4 8,6.6 9,10.6 5.5,8.4 2,10.6 3,6.6 0,4 4,3.8"/></g><use href="#s" x="14"/><use href="#s" x="28"/><use href="#s" x="42"/><use href="#s" x="56"/></svg></div>
  <p class="review-text">“Lorem ipsum dolor sit amet, consectetur ipsum dolor sit amet, consectetur&nbsp; lodr adipiscing elit. Sed vel alique ellentesque justo. Mauris est tortor.”</p>
  <p class="reviewer">Jonah Brandt</p>
</div>
<div class="abs review-card" style="left:458px">
  <svg class="abs quote-mark" width="44" height="40" viewBox="0 0 44 40"><path d="M0 0h18v20l-8 18H2l6-16H0zM24 0h18v20l-8 18h-8l6-16h-8z" fill="var(--orange)"/></svg>
  <div class="stars"><svg width="70" height="11" viewBox="0 0 70 11" fill="var(--gold)"><use href="#s"/><use href="#s" x="14"/><use href="#s" x="28"/><use href="#s" x="42"/><use href="#s" x="56"/></svg></div>
  <p class="review-text">“Lorem ipsum dolor sit amet, consectetur ipsum dolor sit amet, consectetur&nbsp; lodr adipiscing elit. Sed vel alique ellentesque justo. Mauris est tortor.”</p>
  <p class="reviewer">Liam AM</p>
</div>
<div class="abs review-card" style="left:777px">
  <svg class="abs quote-mark" width="44" height="40" viewBox="0 0 44 40"><path d="M0 0h18v20l-8 18H2l6-16H0zM24 0h18v20l-8 18h-8l6-16h-8z" fill="var(--orange)"/></svg>
  <div class="stars"><svg width="70" height="11" viewBox="0 0 70 11" fill="var(--gold)"><use href="#s"/><use href="#s" x="14"/><use href="#s" x="28"/><use href="#s" x="42"/><use href="#s" x="56"/></svg></div>
  <p class="review-text">“Lorem ipsum dolor sit amet, consectetur ipsum dolor sit amet, consectetur&nbsp; lodr adipiscing elit. Sed vel alique ellentesque justo. Mauris est tortor.”</p>
  <p class="reviewer">William WM</p>
</div>

<div class="abs slider-btn slider-prev"><svg width="10" height="14" viewBox="0 0 10 14"><path d="M7 2L2 7l5 5" stroke="#222" stroke-width="2" fill="none"/></svg></div>
<div class="abs slider-btn slider-next"><svg width="10" height="14" viewBox="0 0 10 14"><path d="M3 2l5 5-5 5" stroke="#fff" stroke-width="2" fill="none"/></svg></div>

<!-- tickets -->
<h2 class="abs center tickets">Buy Tickets Online Or<br>Give Us A Call At<svg width="42" height="42" viewBox="0 0 24 24" fill="none" stroke="var(--teal)" stroke-width="1.4"><path d="M6.6 2.5l3 3.2-1.8 2.6c1 2.6 3.3 4.9 5.9 5.9l2.6-1.8 3.2 3-2 3.1C10 18 5.9 13.9 3.5 4.5z"/><path d="M14 2.5a7.5 7.5 0 0 1 7.5 7.5M14 6a4 4 0 0 1 4 4"/></svg>1-800-555-0147</h2>

<!-- footer -->
<footer class="abs footer"></footer>
<div class="abs contact-box" style="left:146px">
  <svg style="margin-top:26px" width="44" height="44" viewBox="0 0 24 24" fill="none" stroke="var(--gold)" stroke-width="1.2"><path d="M6.6 2.5l3 3.2-1.8 2.6c1 2.6 3.3 4.9 5.9 5.9l2.6-1.8 3.2 3-2 3.1C10 18 5.9 13.9 3.5 4.5z"/><path d="M14 2.5a7.5 7.5 0 0 1 7.5 7.5M14 6a4 4 0 0 1 4 4"/></svg>
  <p class="label">Phone</p>
  <p class="value">123.456.7899</p>
</div>
<div class="abs footer-mark" role="img" aria-label="Tour emblem: cocktail glass over a striped desert sunset"></div>
<div class="abs center brand-name footer-name">Calloway Row</div>
<div class="abs contact-box" style="left:848px">
  <svg style="margin-top:26px" width="46" height="44" viewBox="0 0 26 24" fill="none" stroke="var(--gold)" stroke-width="1.2"><path d="M2 9l11-7 11 7v13H2z"/><path d="M2 9l11 8 11-8M2 22l8-7M24 22l-8-7"/><path d="M6 11V5h14v6M9 8h8M9 10.5h8"/></svg>
  <p class="label">Email</p>
  <p class="value">inquiry@callowayrow.com</p>
</div>
<div class="abs follow">
  <span class="follow-text">Follow Us <small>@</small> Calloway</span>
  <span class="social" role="img" aria-label="Social profile link"></span>
  <span class="social" role="img" aria-label="Social profile link"></span>
  <span class="social" role="img" aria-label="Social profile link"></span>
  <span class="social" role="img" aria-label="Social profile link"></span>
</div>
<div class="abs footer-rule"></div>
<p class="abs center copyright">© 2021 <b>Calloway Row Walking Tour.</b> All Rights Reserved.</p>

</body>
</html>
```